Graphic Design Project

We are a new business, Amber Harbour Getaways, specialising in organising and holding professional development retreats in exotic locations (generally outside Australia.) We are targeting professionals and practitioners in the health-related industries (e.g. psychologists, doctors, healing practitioners.)

I need a small brochure (either 3-fold A4 size) or double-sided A4 to promote a retreat we are organising in Bali next year (Coral Spring & Stillness). This retreat focuses on the 3 practices of Buddhism (Nicheren), Mindfulness and Hypnosis, and introduces newcomers to each of these practices. Nichiren Buddhism embraces the practice of chanting (Nam myho ho renge kyo)

We would like the brochure to strike the right balance between visual (nice pictures of Bali and the retreat location at Tamarind Lodges, Bali) and descriptive text content which will give enough information to busy health professionals and appeal to their professional development needs (see attached content draft.)
Updates

Target Market(s)

health care professionals (e.g. clinical psychologists, mental health professionals, doctors, lawyers and anyone in the mental healthcare industries.

Industry/Entity Type

Health

Requirements
Must have
• visuals showing aspects of: Nichiren Buddhism (chanting or hands together with beads pose), massage, contemplation, mindfulness etc, plus images showing retreat location (Tamarind Lodges, Bali). There is a lot of material on the latter's website.
A symbol of Nichiren Buddhism is the lotus flower NOT Buddha.

Colours should be restful and muted.

Ages of people targeted are between 30 and 60.

Follow the Copy draft loosely but feel free to re-arrange the elements to fit the brochure/flyer format

Logo/text style for AMBER HARBOUR GETAWAYS optional. (We don't currently have a logo).

Images are representative only.
Nice to have
• Good (similar) sites that we admire are:
www.quietpalmhaven.com.au
http://www.willowstepjourneys.com.au/workshop-in-bali/bali2013.html
Should not have
• avoid design cliches
No yoga poses
No images of Buddha (Nichiren Buddhism is a humanistic belief system so there is no worship of Buddha himself).
Lotus flower more appropriate.

```html
<!DOCTYPE html>
<html lang="en">
<head>
<meta charset="utf-8">
<title>Coral Spring &amp; Stillness – Amber Harbour Getaways</title>
<link rel="stylesheet" href="https://fonts.googleapis.com/css2?family=Open+Sans:wght@400;700&family=Roboto+Condensed:wght@400;700&family=Roboto+Slab:wght@400;500&family=Tinos&display=swap">
<style>
  :root {
    --green-dark: #0c8043;
    --green-mid: #16a04e;
    --green-bright: #1fae55;
    --green-light: #a5d16a;
    --green-pale: #d6ebb0;
    --orange: #ef7d22;
    --yellow: #f3e53a;
    --white: #ffffff;
    --ink-green: #0f7a3e;
  }
  * { margin: 0; padding: 0; box-sizing: border-box; }
  html, body { width: 1200px; height: 849px; overflow: hidden; background: #ffffff; }
  .brochure {
    position: relative; width: 1200px; height: 849px; overflow: hidden;
    font-family: "Open Sans", Arial, sans-serif;
  }
  .backdrop { position: absolute; inset: 0; }
  .photo { position: absolute; border-radius: 50%; }
  .photo--suite {
    left: -26px; top: 495px; width: 380px; height: 380px;
    background: radial-gradient(circle at 45% 40%, #c9a57a, #7a5436 60%, #4a3322);
  }
  .photo--sunrise {
    left: 388px; top: 231px; width: 194px; height: 194px;
    background: radial-gradient(circle at 50% 70%, #f7d37a, #d9822e 45%, #5e3a2a 80%);
  }
  .photo--lotus {
    left: 1042px; top: 300px; width: 156px; height: 156px;
    background: radial-gradient(circle at 50% 45%, #f2b6d2, #6ea53e 45%, #2f6b2a);
  }
  .photo--meditation {
    left: 802px; top: 485px; width: 398px; height: 250px; border-radius: 0;
    background: linear-gradient(160deg, #b8d38a, #e9e3d3 45%, #7fa35a);
  }

  .fees {
    position: absolute; left: 52px; top: 72px; width: 316px; color: var(--white);
    font-size: 14.3px; line-height: 1.42;
  }
  .fees__title { font-size: 25px; font-weight: 400; margin-bottom: 12px; }
  .fees p + p { margin-top: 30px; }
  .fees b { font-weight: 700; }

  .title-card {
    position: absolute; left: 802px; top: 21px; width: 385px; height: 126px;
    background: var(--white); text-align: center; padding-top: 12px;
  }
  .title-card__name {
    font-family: "Roboto Slab", Georgia, serif; font-weight: 400;
    color: var(--orange); font-size: 35px; line-height: 1.08;
  }
  .title-card__topics {
    margin-top: 6px; font-size: 14.5px; color: var(--ink-green); font-weight: 700;
    display: flex; justify-content: center; gap: 12px;
  }
  .title-card__topics li { list-style: none; }
  .title-card__topics li::before { content: "●"; color: var(--orange); margin-right: 5px; font-size: 12px; }

  .tagline {
    position: absolute; left: 827px; top: 164px; font-family: "Roboto Condensed", Arial, sans-serif;
    color: var(--ink-green); line-height: 1.12;
  }
  .tagline__lead { font-size: 26px; font-weight: 400; }
  .tagline__strong { font-size: 33px; font-weight: 700; }

  .event {
    position: absolute; left: 822px; top: 328px; width: 200px; text-align: center;
    font-family: "Tinos", "Times New Roman", serif; color: var(--white); font-size: 20px; line-height: 1.35;
  }
  .event__venue { margin-bottom: 8px; }

  .brand {
    position: absolute; display: flex; align-items: center; gap: 8px;
    font-family: "Roboto Slab", Georgia, serif; font-weight: 500; color: var(--ink-green);
    font-size: 19px; line-height: 1.1;
  }
  .brand__dot { width: 44px; height: 44px; border-radius: 50%; background: var(--green-bright); flex: none; }
  .brand--contact { left: 445px; top: 540px; width: 300px; }
  .brand--footer { left: 968px; top: 748px; width: 228px; }

  .contact {
    position: absolute; left: 450px; top: 622px; color: var(--ink-green); font-weight: 700;
    font-size: 14px; line-height: 1.55;
  }
  .contact__label { font-size: 17px; }
  .contact__lines { margin-bottom: 12px; }
  .contact__row { display: flex; font-size: 16px; line-height: 1.38; }
  .contact__row span:first-child { width: 78px; }

  .footer-strip {
    position: absolute; left: 385px; top: 823px; width: 815px; height: 26px;
    background: var(--green-dark);
  }
  .footer-strip__url {
    position: absolute; right: 14px; top: 4px; color: var(--yellow); font-weight: 700; font-size: 14px;
  }
</style>
</head>
<body>
<main class="brochure">
  <svg class="backdrop" width="1200" height="849" viewBox="0 0 1200 849" aria-hidden="true">
    <defs>
      <linearGradient id="middle-wash" x1="0" y1="0" x2="0" y2="1">
        <stop offset="0" stop-color="#cfe6a2"/>
        <stop offset="0.55" stop-color="#eef6df"/>
        <stop offset="1" stop-color="#ffffff"/>
      </linearGradient>
    </defs>
    <rect x="385" y="0" width="815" height="849" fill="url(#middle-wash)"/>
    <rect x="800" y="0" width="400" height="849" fill="#ffffff"/>
    <!-- middle panel arcs -->
    <circle cx="900" cy="130" r="420" fill="var(--green-light)"/>
    <circle cx="900" cy="130" r="395" fill="#ffffff"/>
    <circle cx="900" cy="130" r="380" fill="var(--green-mid)"/>
    <rect x="385" y="470" width="415" height="380" fill="#ffffff" opacity="0.55"/>
    <!-- right panel -->
    <rect x="800" y="0" width="400" height="485" fill="var(--green-mid)"/>
    <circle cx="930" cy="150" r="170" fill="var(--green-light)"/>
    <circle cx="1120" cy="378" r="118" fill="var(--green-dark)"/>
    <circle cx="1120" cy="378" r="92" fill="#ffffff"/>
    <rect x="800" y="735" width="400" height="90" fill="#ffffff"/>
    <!-- left panel -->
    <rect x="0" y="0" width="385" height="849" fill="var(--green-dark)"/>
    <circle cx="164" cy="685" r="228" fill="#ffffff"/>
    <circle cx="164" cy="685" r="218" fill="var(--green-light)"/>
    <circle cx="164" cy="685" r="196" fill="#ffffff"/>
    <!-- sunrise ring -->
    <circle cx="485" cy="328" r="130" fill="var(--green-light)"/>
    <circle cx="485" cy="328" r="108" fill="#ffffff"/>
  </svg>

  <div class="photo photo--suite" role="img" aria-label="Villa bedroom with four-poster bed opening onto a garden"></div>
  <div class="photo photo--sunrise" role="img" aria-label="Silhouette meditating with raised arms against a mountain sunrise"></div>
  <div class="photo photo--lotus" role="img" aria-label="Pink lotus flower among green leaves"></div>
  <div class="photo photo--meditation" role="img" aria-label="Two people meditating cross-legged in a tropical garden"></div>

  <section class="fees">
    <h2 class="fees__title">Fees and Inclusions</h2>
    <p><b>Cost:</b> $1850 incl. GST, *accommodation, *meals, and massage – Spaces limited to 14 people. Save 10% Early Bird Special (pay $1665 if booked before 1st of Feb. 2013) and an additional 10% (pay $1480) if you bring a friend.</p>
    <p>*Includes 4 nights accommodation, materials, all breakfasts &amp; lunches as well as 1 final night group dinner in one of Ubud's boutique restaurants. <b>Deposit:</b> $500. Bookings are transferable, however deposit is non-refundable.</p>
  </section>

  <header class="title-card">
    <h1 class="title-card__name">Coral Spring &amp;<br>Stillness</h1>
    <ul class="title-card__topics">
      <li>Buddhism</li><li>Mindfulness</li><li>Hypnosis</li>
    </ul>
  </header>

  <div class="tagline">
    <div class="tagline__lead">PROFESSIONAL<br>DEVELOPMENT IN A</div>
    <div class="tagline__strong">RETREAT SETTING</div>
  </div>

  <div class="event">
    <div class="event__venue">Tamarind Lodges Bali</div>
    <div>29 March to<br>1 April 2013</div>
  </div>

  <div class="brand brand--contact"><span class="brand__dot"></span><span>AMBER HARBOUR GETAWAYS</span></div>

  <address class="contact">
    <div class="contact__label">Address :</div>
    <div class="contact__lines">Your address here<br>Your address here<br>Your address here</div>
    <div class="contact__row"><span>Phone:</span><span>021547 30218</span></div>
    <div class="contact__row"><span>Fax:</span><span>021547 30218</span></div>
    <div class="contact__row"><span>Email :</span><span>info@amberharbourgetaways.com</span></div>
  </address>

  <div class="brand brand--footer"><span class="brand__dot"></span><span>AMBER HARBOUR GETAWAYS</span></div>

  <footer class="footer-strip">
    <span class="footer-strip__url">www.amber-harbour-getaways.com</span>
  </footer>
</main>
</body>
</html>
```